I have a haircare line called Velmora Professional. I’m branching out to create a line of Humanistic haircare products for pets. I want it to look similar to my Velmora haircare Line. By adding some type of creative way of incorporating the word Pet. I am also attaching an image of Dorian Kessler Pet. I do not want it to look too similar to this as our looks are both clean and contemporary. I also am entertaining changing the bottles from cylinder to boston round. I will attach my new haircare packaging aswell. Please note that the boston round bottles are the round bottles attached not the tall square ones. They can be made black or white or natural plastic. Please use this shape to come up with a thought. I do what to keep my black and white motif. The word Pet can be maybe made bold to stand out but think fun and maybe some type of symbol that creates a pet theme. I also do the conditioner in the reverse color of the shampoo which makes the shampoo/conditioner package. Please keep this in mind aswell.

Target Market(s)

Boutique pet stores, Furvana

Industry/Entity Type

Hair Care Product

Logo Text

Velmora Pro Pet

Colors

Designer to choose colors to be used in the design.

Requirements
Must have
• Shampoo/conditioner designs
Nice to have
• Want to keep the black and white motif but open to new ideas aswell
Should not have
• Should look expensive and modern

```html
<!DOCTYPE html>
<html lang="en">
<head>
<meta charset="UTF-8">
<title>Velmora Professional Pet — Shampoo &amp; Conditioner Labels</title>
<link rel="stylesheet" href="https://fonts.googleapis.com/css2?family=Oswald:wght@400;500;600&family=Raleway:wght@300;400&family=Pathway+Gothic+One&family=Montserrat:wght@600&display=swap">
<style>
  :root {
    --backdrop: #d9dcdf;
    --white: #ffffff;
    --black: #0d0d0d;
    --ink-dark: #1a1a1a;
    --ink-light: #f2f2f2;
    --grey-text: #8a8a8a;
    --teal: #2a9ba8;
  }
  * { box-sizing: border-box; margin: 0; padding: 0; }
  html, body {
    width: 1200px; height: 1200px; overflow: hidden;
    background: var(--backdrop);
  }
  .label-set {
    position: relative; width: 1200px; height: 1200px;
    display: flex; justify-content: center; align-items: center; gap: 40px;
  }
  .label {
    position: relative; width: 540px; height: 760px;
    display: grid; grid-template-columns: 100px 1fr 100px;
    padding: 40px 14px;
    column-gap: 14px;
  }
  .label--conditioner { background: var(--white); color: var(--ink-dark); --frame: var(--black); }
  .label--shampoo { background: var(--black); color: var(--ink-light); --frame: var(--white); }

  .side-copy {
    font-family: "Pathway Gothic One", sans-serif;
    font-size: 12.5px; line-height: 1.45;
    overflow: hidden;
    display: flex; flex-direction: column;
  }
  .side-copy p + p { margin-top: 22px; }
  .side-copy strong { font-weight: 400; text-transform: uppercase; }
  .side-copy--left { justify-content: space-between; padding-top: 30px; }
  .legal { font-size: 11px; text-transform: uppercase; }
  .side-copy--right { padding-top: 30px; }

  .front-panel {
    border: 3px solid var(--frame);
    display: flex; flex-direction: column; align-items: center;
    padding: 70px 16px 24px;
    text-align: center;
  }
  .brand-dot {
    width: 70px; height: 70px; border-radius: 50%;
    border: 3px solid currentColor;
    margin-bottom: 34px;
  }
  .brand-name {
    font-family: "Raleway", sans-serif; font-weight: 400;
    font-size: 40px; letter-spacing: 1px; line-height: 1;
    text-transform: uppercase;
  }
  .brand-sub {
    font-family: "Raleway", sans-serif; font-weight: 400;
    font-size: 13px; letter-spacing: 6.5px; line-height: 1;
    text-transform: uppercase; margin-top: 6px;
    color: var(--grey-text);
  }
  .line-name {
    font-family: "Raleway", sans-serif; font-weight: 300;
    font-size: 104px; line-height: 1; color: var(--teal);
    letter-spacing: 2px; margin-top: 14px;
  }
  .product-type {
    font-family: "Oswald", sans-serif; font-weight: 600;
    font-size: 24px; letter-spacing: 0.5px; margin-top: 4px;
    text-transform: uppercase;
  }
  .claims {
    font-family: "Oswald", sans-serif; font-weight: 400;
    margin-top: 54px; line-height: 1.2;
  }
  .claims .claim-main { font-size: 17px; }
  .claims .claim-small { font-size: 12.5px; }
  .claims .claim-mid { font-size: 16px; }
  .volume {
    font-family: "Montserrat", sans-serif; font-weight: 600;
    font-size: 11.5px; letter-spacing: 0.5px;
    margin-top: auto;
  }
</style>
</head>
<body>
<main class="label-set">

  <section class="label label--conditioner" aria-label="Pet conditioner label">
    <div class="side-copy side-copy--left">
      <p>Crafted by groomers for coats that shine. Gentle botanicals cleanse without stripping natural oils, leaving fur soft, light and easy to brush. Safe for regular use on cats and dogs of every age.</p>
      <p class="legal">© Velmora Professional, LLC</p>
    </div>

    <div class="front-panel">
      <div class="brand-dot" aria-hidden="true"></div>
      <div class="brand-name">Velmora</div>
      <div class="brand-sub">Professional</div>
      <div class="line-name">PET</div>
      <div class="product-type">Conditioner</div>
      <div class="claims">
        <div class="claim-main">Paraben Free</div>
        <div class="claim-small">Contains Certified Organic Extracts</div>
        <div class="claim-main">Vegan</div>
        <div class="claim-mid">CATS+DOGS</div>
      </div>
      <div class="volume">32 fl oz 946 mL</div>
    </div>

    <div class="side-copy side-copy--right">
      <p>Now your pet's hair can look as good as yours does! <strong>Pet Conditioner</strong> restores your pet's coat after <strong>Pet Shampoo</strong>. Deeply infused to replenish hair for a youthful shine.</p>
      <p><strong>Directions:</strong> Apply to mid-lengths and ends. Leave on 2 minutes. Rinse thoroughly.</p>
      <p><strong>Ingredients:</strong> Aqua, cetearyl alcohol, glycerin, aloe leaf juice, coconut oil, shea butter, panthenol, oat protein, chamomile extract, lavender oil, citric acid.</p>
    </div>
  </section>

  <section class="label label--shampoo" aria-label="Pet shampoo label">
    <div class="side-copy side-copy--left">
      <p>Crafted by groomers for coats that shine. Gentle botanicals cleanse without stripping natural oils, leaving fur soft, light and easy to brush. Safe for regular use on cats and dogs of every age.</p>
      <p class="legal">© Velmora Professional, LLC</p>
    </div>

    <div class="front-panel">
      <div class="brand-dot" aria-hidden="true"></div>
      <div class="brand-name">Velmora</div>
      <div class="brand-sub">Professional</div>
      <div class="line-name">PET</div>
      <div class="product-type">Shampoo</div>
      <div class="claims">
        <div class="claim-main">Sulfate+Paraben Free</div>
        <div class="claim-small">Contains Certified Organic Extracts</div>
        <div class="claim-main">Vegan</div>
        <div class="claim-mid">CATS+DOGS</div>
      </div>
      <div class="volume">32 fl oz 946 mL</div>
    </div>

    <div class="side-copy side-copy--right">
      <p>Now your pet's hair can look as good as yours does! <strong>Pet Shampoo</strong> with peptides, antioxidants and botanicals to improve the manageability of hair. It will make your pet feel VELMORA!</p>
      <p><strong>Directions:</strong> Wet coat. Lather from skin to ends. Rinse thoroughly.</p>
      <p><strong>Ingredients:</strong> Aqua, coco glucoside, decyl glucoside, glycerin, aloe leaf juice, oat protein, panthenol, chamomile extract, rosemary oil, citric acid.</p>
    </div>
  </section>

</main>
</body>
</html>
```